Web design project for exciting Australian start-up

Background
We are looking for a creative and talented web design artist to work alongside our market leading web developer.
• You will be required to create a modern and clean design theme for our website, incorporating selected rustic colour scheme elements for our exciting Australian start-up to operate within the coffee industry.
reoccurring work to be expected to flow to the successful designer.
Requirements
• c. 5 - 10 page website
• Landing page
• Log in/ out
• 404 template
• Typography is emphasised
• Please use either a) typemarrow.com, b) free web fonts, c) brindle fonts
• All design elements in vector format
• Preferably with icons for each header title(i.e. about us, how it works etc) but designer have free reign over how the site looks, so might not be applicable
• All pages to be responsive
• Down to eSlab resolution

High level visual design brief attached - additional pages to be worked from base design.

Design inspiration
• We would like to use design elements from the following sources:
http://www.zandrix.com/halcyon/ (Functionality)
Colour scheme refer to logo and complementary style guide

```html
<!DOCTYPE html>
<html lang="en">
<head>
<meta charset="utf-8">
<title>Brewhaven – Marketplace</title>
<link href="https://fonts.googleapis.com/css2?family=Roboto:wght@300;400;500&family=Source+Sans+3:wght@400;600&display=swap" rel="stylesheet">
<style>
:root{
  --orange:#f7a21b;
  --orange-deep:#d97a2e;
  --ink:#222;
  --text:#333;
  --muted:#8a8a8a;
  --rule:#e3e3e3;
  --white:#fff;
  --option-hi:#a9a9a9;
  --footer-bg:#f4f4f4;
}
*{box-sizing:border-box;margin:0;padding:0}
html,body{width:1200px;height:1068px;overflow:hidden;background:var(--white)}
body{position:relative;font-family:"Roboto",sans-serif;color:var(--text)}
.abs{position:absolute}

.top-strip{left:0;top:0;width:1200px;height:4px;background:var(--orange)}
.brand{left:105px;top:44px;display:flex;align-items:center;gap:10px}
.brand-dot{width:40px;height:40px;border-radius:50%;background:var(--orange)}
.brand-name{font-family:"Roboto",sans-serif;font-weight:500;font-size:26px;letter-spacing:2px;color:var(--ink)}
.auth{left:960px;top:49px;height:31px;display:flex;border:1px solid #333}
.auth a{display:flex;align-items:center;justify-content:center;font-size:14px;font-weight:300;color:var(--ink);text-decoration:none;height:100%}
.auth a.login{width:76px;border-right:1px solid #333}
.auth a.signup{width:86px}

.hero{left:0;top:123px;width:1200px;height:491px;overflow:hidden;
  background:
   radial-gradient(ellipse 260px 200px at 300px 200px,#e9e4dc 0%,#cfc5b8 45%,rgba(120,90,60,0) 100%),
   radial-gradient(ellipse 300px 240px at 820px 220px,#d8d2c8 0%,rgba(150,130,110,.6) 55%,rgba(90,60,40,0) 100%),
   linear-gradient(120deg,#6b4a30 0%,#9b7d62 30%,#a79583 55%,#6e5a48 80%,#4a3526 100%)}
.hero-photo{left:0;top:0;width:1200px;height:491px}
.panel-rule{top:0;width:1px;height:491px;background:rgba(255,255,255,.8)}
.marketplace{left:101px;top:280px;font-weight:300;font-size:63px;color:var(--white)}
.btn-tender{left:104px;top:366px;width:217px;height:50px;border:2px solid var(--white);border-radius:3px;
  display:flex;align-items:center;gap:14px;padding-left:18px;color:var(--white);font-weight:500;font-size:17px;letter-spacing:.3px}

.select-title{left:536px;top:17px;font-weight:300;font-size:34px;color:var(--white)}
.select-rule{left:536px;top:66px;width:527px;height:1px;background:rgba(255,255,255,.7)}
.dropdown{height:35px;background:var(--white);display:flex;font-size:22px;color:#111;box-shadow:0 1px 3px rgba(0,0,0,.25)}
.dropdown span{flex:1;padding-left:12px;display:flex;align-items:center}
.dropdown .caret{width:38px;border-left:1px solid #ddd;display:flex;align-items:center;justify-content:center}
.options{background:var(--white);box-shadow:0 1px 3px rgba(0,0,0,.25)}
.options li{list-style:none;height:35px;display:flex;align-items:center;padding-left:16px;font-weight:300;font-size:22px;color:#111}
.options li.active{background:var(--option-hi);color:#eee}
.btn-search{left:839px;top:389px;width:226px;height:55px;border:3px solid rgba(255,255,255,.55);border-radius:3px;
  background:linear-gradient(180deg,#e89a55,var(--orange-deep));display:flex;align-items:center;gap:12px;padding-left:16px;
  color:var(--white);font-weight:500;font-size:17px}

.col{top:646px;width:240px;text-align:center}
.avatar{width:106px;height:106px;border-radius:50%;margin:0 auto}
.col h2{font-family:"Source Sans 3",sans-serif;font-weight:600;font-size:24px;color:#333;margin-top:22px}
.links{width:141px;margin:12px auto 0;list-style:none}
.links li{height:34.5px;border-bottom:1px solid var(--rule);display:flex;align-items:center;justify-content:center;
  font-family:"Source Sans 3",sans-serif;font-size:15px;color:var(--muted);gap:8px}
.links li .tri{width:0;height:0;border-left:5px solid transparent;border-right:5px solid transparent;border-top:6px solid var(--orange)}
.divider{top:700px;width:8px;height:250px;background:radial-gradient(ellipse 3px 50% at 0 50%,rgba(0,0,0,.14),rgba(0,0,0,0))}
.social{left:855px;top:812px;width:139px;list-style:none}
.social li{height:38.5px;border-bottom:1px solid var(--rule);display:flex;align-items:center;
  font-family:"Source Sans 3",sans-serif;font-size:15px;color:var(--muted)}
.social li i{width:27px;height:27px;border-radius:50%;background:var(--orange);margin-right:0}
.social li b{flex:1;text-align:center;font-weight:400}

.site-footer{left:0;top:1021px;width:1200px;height:47px;background:var(--footer-bg);border-top:1px solid #dde6e6}
.site-footer p{position:absolute;left:115px;top:16px;font-size:11px;color:#444}
</style>
</head>
<body>
<div class="abs top-strip"></div>

<header>
  <div class="abs brand"><span class="brand-dot"></span><span class="brand-name">BREWHAVEN</span></div>
  <nav class="abs auth"><a class="login" href="#">Login</a><a class="signup" href="#">Sign Up</a></nav>
</header>

<section class="abs hero">
  <div class="abs hero-photo" role="img" aria-label="Blurred close-up photo of a white coffee cup with coffee beans"></div>
  <div class="abs panel-rule" style="left:465px"></div>
  <div class="abs panel-rule" style="left:1131px"></div>

  <h1 class="abs marketplace">Marketplace</h1>
  <div class="abs btn-tender">
    <svg width="24" height="24" viewBox="0 0 24 24" fill="none" stroke="#fff" stroke-width="1.6">
      <circle cx="12" cy="12" r="3.5"/>
      <path d="M12 2l1.6 2.8 3.1-.9.6 3.2 3 1.2-1.3 3 2 2.5-2.8 1.6.4 3.2-3.2.2-1.2 3-2.9-1.4-2.5 2-1.6-2.8-3.2.4-.2-3.2-3-1.2 1.4-2.9-2-2.5 2.8-1.6-.4-3.2 3.2-.2 1.2-3 2.9 1.4z"/>
    </svg>
    START A TENDER
  </div>

  <div class="abs select-title">Select</div>
  <div class="abs select-rule"></div>

  <div class="abs dropdown" style="left:536px;top:90px;width:216px"><span>Tender Type</span><div class="caret"><svg width="14" height="9"><path d="M0 0h14L7 9z" fill="#bbb"/></svg></div></div>
  <ul class="abs options" style="left:756px;top:90px;width:153px">
    <li>One-off</li><li class="active">Recurring</li>
  </ul>
  <ul class="abs options" style="left:909px;top:126px;width:154px">
    <li>6 months</li><li>12 months</li>
  </ul>

  <div class="abs dropdown" style="left:536px;top:148px;width:216px"><span>Quantity (kg)</span><div class="caret"><svg width="9" height="14"><path d="M0 0v14l9-7z" fill="#bbb"/></svg></div></div>

  <div class="abs dropdown" style="left:535px;top:208px;width:217px"><span>Wholesaler</span><div class="caret"><svg width="14" height="9"><path d="M0 0h14L7 9z" fill="#bbb"/></svg></div></div>
  <ul class="abs options" style="left:755px;top:208px;width:154px">
    <li>Marretti</li><li class="active">Del Sorro</li><li>Caffix</li><li>Valtorra</li>
  </ul>
  <ul class="abs options" style="left:909px;top:244px;width:153px">
    <li>Blend A</li><li>Blend B</li>
  </ul>

  <div class="abs btn-search">
    <svg width="20" height="20" viewBox="0 0 20 20"><circle cx="8" cy="8" r="5.5" fill="none" stroke="#fff" stroke-width="2.6"/><path d="M12 12l6 6" stroke="#fff" stroke-width="3.2" stroke-linecap="round"/></svg>
    LAUNCH A SEARCH
  </div>
</section>

<section class="abs col" style="left:119px">
  <div class="avatar" role="img" aria-label="Black and white photo of a steaming coffee cup" style="background:radial-gradient(circle at 45% 55%,#ddd,#555 60%,#222)"></div>
  <h2>Helpful Info</h2>
  <ul class="links">
    <li><span class="tri"></span>About us</li><li>Media Enquiries</li><li>Terms &amp; Conditions</li><li>Privacy Policy</li>
  </ul>
</section>
<div class="abs divider" style="left:407px"></div>
<section class="abs col" style="left:460px">
  <div class="avatar" role="img" aria-label="Black and white portrait of a team member" style="background:radial-gradient(circle at 50% 40%,#bbb,#555 55%,#1c1c1c)"></div>
  <h2>Who We Are</h2>
  <ul class="links">
    <li><span class="tri"></span>How It Works</li><li>FAQ</li><li>Contact Us</li>
  </ul>
</section>
<div class="abs divider" style="left:758px"></div>
<section class="abs col" style="left:810px">
  <div class="avatar" role="img" aria-label="Black and white photo of a cup filled with coffee beans" style="background:radial-gradient(circle at 50% 70%,#f2f2f2,#999 45%,#2a2a2a)"></div>
  <h2>Join Us On</h2>
</section>
<ul class="abs social">
  <li><i></i><b>Pagebook</b></li>
  <li><i></i><b>Chirper</b></li>
  <li><i></i><b>Linkwise</b></li>
  <li><i></i><b>Tubecast</b></li>
</ul>

<footer class="abs site-footer"><p>Copyright © 2014 Brewhaven</p></footer>
</body>
</html>
```